BWP Business Card

A double sided business card based on your "Brindlewood Partners Ltd" Logo. To use the "BWP" logo on 1 side and the full company logo on the reverse.

Detials to be included:

Name: Tomas Wheeler
Postion: Consultant Orthotist & Expert Witness
T: +44 (0) 7700 938271
F: +44 (0) 7654 8820

```html
<!DOCTYPE html>
<html lang="en">
<head>
<meta charset="utf-8">
<title>Brindlewood Partners Ltd – Business Card</title>
<link rel="stylesheet" href="https://fonts.googleapis.com/css2?family=Tinos:wght@400;700&display=swap">
<style>
  :root {
    --navy: #1f3f73;
    --grey: #a3a5a8;
    --white: #ffffff;
    --page: #ecebe8;
    --ink-light: #e6ebf3;
  }
  * { box-sizing: border-box; margin: 0; padding: 0; }
  html, body { width: 1200px; height: 720px; overflow: hidden; }
  body {
    background: var(--page);
    position: relative;
    font-family: "Tinos", "Times New Roman", serif;
  }
  .card {
    position: absolute;
    top: 210px;
    width: 520px;
    height: 300px;
    background: var(--white);
    box-shadow: 0 6px 18px rgba(0,0,0,0.18);
    overflow: hidden;
  }
  .card--front { left: 60px; }
  .card--back { left: 620px; }

  /* Company name with plain square */
  .brand {
    position: absolute;
    display: flex;
    align-items: center;
    white-space: nowrap;
  }
  .brand__square { background: var(--navy); flex: none; }
  .brand__name {
    font-family: "Tinos", "Times New Roman", serif;
    font-weight: 700;
    color: var(--navy);
  }

  .card--front .brand { left: 90px; top: 48px; gap: 18px; }
  .card--front .brand__square { width: 52px; height: 52px; }
  .card--front .brand__name { font-size: 28px; }

  .card--back .brand { left: 0; right: 0; top: 110px; justify-content: center; gap: 22px; }
  .card--back .brand__square { width: 72px; height: 72px; }
  .card--back .brand__name { font-size: 36px; }

  /* Contact bands */
  .name-band {
    position: absolute;
    left: 0; right: 0;
    top: 148px;
    height: 30px;
    background: var(--grey);
    padding-left: 40px;
    display: flex;
    align-items: center;
    color: var(--white);
    font-size: 15px;
  }
  .name-band__name { font-weight: 700; font-size: 17px; }
  .name-band__role { margin-left: 6px; }

  .contact-band {
    position: absolute;
    left: 0; right: 0;
    top: 178px;
    bottom: 0;
    background: var(--navy);
    color: var(--ink-light);
    display: flex;
    align-items: center;
    font-size: 14px;
  }
  .address {
    width: 220px;
    text-align: right;
    padding-right: 14px;
    line-height: 1.5;
    font-style: normal;
  }
  .contact-band__divider {
    width: 1px;
    height: 70px;
    background: var(--ink-light);
    opacity: 0.7;
  }
  .contact-list {
    list-style: none;
    padding-left: 14px;
    line-height: 1.55;
  }
  .contact-list li { display: flex; align-items: center; gap: 7px; }
  .contact-list svg { width: 12px; height: 12px; fill: var(--ink-light); flex: none; }
</style>
</head>
<body>

  <section class="card card--front" aria-label="Business card, contact side">
    <div class="brand">
      <div class="brand__square"></div>
      <div class="brand__name">Brindlewood Partners Ltd</div>
    </div>

    <div class="name-band">
      <span class="name-band__name">Tomas Wheeler,</span>
      <span class="name-band__role">Consultant Orthotist &amp; Expert Witness</span>
    </div>

    <div class="contact-band">
      <address class="address">14 Larkspur Road Kingsford<br>Surrey, KT9 4QD</address>
      <div class="contact-band__divider"></div>
      <ul class="contact-list">
        <li>
          <svg viewBox="0 0 24 24" aria-hidden="true"><path d="M6.6 10.8a15 15 0 0 0 6.6 6.6l2.2-2.2a1 1 0 0 1 1-.25 11.4 11.4 0 0 0 3.6.57 1 1 0 0 1 1 1V20a1 1 0 0 1-1 1A17 17 0 0 1 3 4a1 1 0 0 1 1-1h3.5a1 1 0 0 1 1 1c0 1.25.2 2.45.57 3.57a1 1 0 0 1-.25 1z"/></svg>
          +44 (0) 7700 938271
        </li>
        <li>
          <svg viewBox="0 0 24 24" aria-hidden="true"><path d="M6 2h12v6H6z M4 9h16a2 2 0 0 1 2 2v6h-4v4H6v-4H2v-6a2 2 0 0 1 2-2z M8 15v4h8v-4z"/></svg>
          +44 (0) 7654 8820
        </li>
        <li>
          <svg viewBox="0 0 24 24" aria-hidden="true"><path d="M2 5h20v14H2z M4 7v.5l8 5 8-5V7z" fill-rule="evenodd"/></svg>
          tomas@brindlewoodpartners.co.uk
        </li>
      </ul>
    </div>
  </section>

  <section class="card card--back" aria-label="Business card, company name side">
    <div class="brand">
      <div class="brand__square"></div>
      <div class="brand__name">Brindlewood Partners Ltd</div>
    </div>
  </section>

</body>
</html>
```